Salon and Spa Distributor Business Card

Need a business card. We are are distributor in the salon and spa industry. We identify with natural beauty. Need a card with:
Company Name: Petal Quarry"
Title: "President & CEO"
Address
Company Phone number
email
website
Tag Line:" The Professional Salon Source"

Industry/Entity Type

Business

Contact Information for Business Card

Name: Dov Strommen
Title: "President & CEO"
Address: 31 Harlow Ln, Bexmoor, NJ 07813
Company Phone number: 800-463-5918
email: dovstrommen@petalquarry.example
website: www.petalquarry.example

Requirements
Should not have
• No black backgrounds

```html
<!DOCTYPE html>
<html lang="en">
<head>
<meta charset="utf-8">
<title>Petal Quarry – Business Card</title>
<link rel="stylesheet" href="https://fonts.googleapis.com/css2?family=Questrial&display=swap">
<style>
  :root {
    --page: #e4e5e4;
    --green-deep: #0a5d2b;
    --green-mid: #2f7a3a;
    --green-bright: #3aa535;
    --green-text: #1d6b2c;
    --ink: #555a55;
    --card-white: #f6f6f5;
    --white: #ffffff;
  }
  * { margin: 0; padding: 0; box-sizing: border-box; }
  html, body {
    width: 1200px; height: 576px; overflow: hidden;
    background: var(--page);
    font-family: "Questrial", "Century Gothic", sans-serif;
  }
  .canvas { position: relative; width: 1200px; height: 576px; }

  .card {
    position: absolute; top: 138px;
    height: 293px; border-radius: 11px; overflow: hidden;
  }

  /* Front */
  .card-front {
    left: 82px; width: 484px;
    background: linear-gradient(180deg, var(--green-deep) 0%, var(--green-mid) 100%);
  }
  .front-mark {
    position: absolute; left: 50%; top: 86px;
    width: 56px; height: 56px; margin-left: -28px;
    border-radius: 50%; background: var(--white);
  }
  .front-name {
    position: absolute; left: 0; right: 0; top: 185px;
    text-align: center; color: var(--white);
    font-size: 30px; letter-spacing: 0.2px;
  }

  /* Back */
  .card-back { left: 602px; width: 481px; background: var(--card-white); }
  .stripe-deep { position: absolute; left: 0; top: 0; bottom: 0; width: 40px; background: var(--green-deep); }
  .stripe-bright { position: absolute; left: 40px; top: 0; bottom: 0; width: 5px; background: var(--green-bright); }

  .brand { position: absolute; left: 226px; top: 42px; display: flex; align-items: center; gap: 12px; }
  .brand-dot { width: 36px; height: 36px; border-radius: 50%; background: var(--green-bright); }
  .brand-name { color: var(--green-text); font-size: 27px; line-height: 1; }
  .brand-tagline { color: var(--ink); font-size: 12px; margin-top: 6px; }

  .holder { position: absolute; left: 68px; top: 139px; }
  .holder-name { color: var(--green-text); font-size: 24px; line-height: 1; }
  .holder-title { color: var(--ink); font-size: 11px; margin-top: 5px; }

  .contacts { position: absolute; left: 68px; top: 199px; list-style: none; }
  .contacts li {
    display: flex; align-items: center; gap: 8px;
    height: 18.5px; color: var(--ink); font-size: 13.5px;
  }
  .contacts svg { width: 11px; height: 11px; fill: var(--green-deep); flex: none; }
  .contacts .address { padding-left: 0; }
</style>
</head>
<body>
<main class="canvas">
  <section class="card card-front" aria-label="Card front">
    <div class="front-mark"></div>
    <p class="front-name">Petal Quarry</p>
  </section>

  <section class="card card-back" aria-label="Card back">
    <div class="stripe-deep"></div>
    <div class="stripe-bright"></div>

    <div class="brand">
      <div class="brand-dot"></div>
      <div>
        <p class="brand-name">Petal Quarry</p>
        <p class="brand-tagline">The Professional Salon Source</p>
      </div>
    </div>

    <div class="holder">
      <p class="holder-name">Petal Quarry</p>
      <p class="holder-title">President &amp; CEO</p>
    </div>

    <ul class="contacts">
      <li>
        <svg viewBox="0 0 12 12" aria-hidden="true"><path d="M1 4.5C1 2.5 3 1.5 6 1.5S11 2.5 11 4.5L9 5 8.3 3.8H3.7L3 5Z M3 6h6l1.5 4.5h-9Z"/></svg>
        800-463-5918
      </li>
      <li>
        <svg viewBox="0 0 12 12" aria-hidden="true"><path d="M0.5 2.5h11v7h-11Z M1.5 3.3 6 6.8l4.5-3.5" fill="none" stroke="#0a5d2b" stroke-width="1.2"/></svg>
        dovstrommen@petalquarry.example
      </li>
      <li>
        <svg viewBox="0 0 12 12" aria-hidden="true"><circle cx="6" cy="6" r="5.2" fill="none" stroke="#0a5d2b" stroke-width="1.1"/><path d="M0.8 6h10.4M6 0.8c-3 3-3 7.4 0 10.4M6 0.8c3 3 3 7.4 0 10.4" fill="none" stroke="#0a5d2b" stroke-width="1"/></svg>
        www.petalquarry.example
      </li>
      <li class="address">31 Harlow Ln, Bexmoor, NJ 07813</li>
    </ul>
  </section>
</main>
</body>
</html>
```